Fern Lattice Table & Chair Rentals

We need a business card for a table and chair rental company. We rent tables and chairs for weddings, funerals, business events and parties. We want something that looks clean and elegant while not being too busy. We would like colors in the green and blue hues and avoiding anything orange. We want to make sure the font is large enough to be seen easily.

Target Market(s)

Wedding & Event Rentals

Industry/Entity Type

Events

Contact Information for Business Card

Fern Lattice, sales@fernlatticerentals.com, fernlatticerentals.com, 360-555-0182

Requirements
Must have
• Easy to read font
Should not have
• Orange anywhere in the design

```html
<!DOCTYPE html>
<html lang="en">
<head>
<meta charset="utf-8">
<title>Fern Lattice Table &amp; Chair Rentals – Business Card</title>
<link href="https://fonts.googleapis.com/css2?family=Montserrat:wght@400;500&display=swap" rel="stylesheet">
<style>
  :root {
    --backdrop: #e9eae7;
    --card-white: #ffffff;
    --ink: #2a241c;
    --earth: #3b3324;
    --leaf: #6c9a1f;
    --leaf-light: #8fb83a;
    --on-dark: #f4f2ec;
  }
  * { margin: 0; padding: 0; box-sizing: border-box; }
  html, body {
    width: 1200px; height: 852px; overflow: hidden;
    background: var(--backdrop);
    font-family: "Montserrat", Arial, sans-serif;
    color: var(--ink);
  }
  .sheet {
    position: relative; width: 1200px; height: 852px;
    display: flex; flex-direction: column; align-items: center; justify-content: center; gap: 60px;
  }
  .card {
    position: relative; width: 540px; height: 300px;
    border-radius: 16px; overflow: hidden;
    background: var(--card-white);
    box-shadow: 0 4px 14px rgba(0,0,0,0.12);
  }
  .brand {
    position: absolute;
    display: flex; flex-direction: column; align-items: flex-start;
    white-space: nowrap;
  }
  .brand-name { font-weight: 500; line-height: 1; color: var(--ink); letter-spacing: 0.5px; }
  .brand-tagline { font-weight: 400; color: var(--ink); margin-top: 10px; line-height: 1.1; }

  /* Front */
  .card-front .photo {
    position: absolute; inset: 0;
    background:
      radial-gradient(circle at 58% 48%, #f7f8f4 0 12%, #dfe7dc 22%, transparent 40%),
      radial-gradient(circle at 16% 62%, #e6ece4 0 9%, transparent 20%),
      radial-gradient(circle at 32% 58%, #eef1ec 0 8%, transparent 18%),
      linear-gradient(160deg, #f2f3f0 0%, #d9dcd4 45%, #8f9a7c 75%, #4f6a2a 100%);
  }
  .card-front .brand { left: 150px; top: 100px; }
  .card-front .brand-name { font-size: 44px; }
  .card-front .brand-tagline { font-size: 22px; }

  /* Back */
  .card-back .photo-faint {
    position: absolute; inset: 0;
    background: radial-gradient(circle at 45% 40%, #f1f4ef 0 20%, transparent 55%), var(--card-white);
  }
  .card-back .brand { left: 40px; top: 95px; }
  .card-back .brand-name { font-size: 40px; }
  .card-back .brand-tagline { font-size: 19px; }
  .corner-name {
    position: absolute; right: 60px; top: 22px;
    font-weight: 500; font-size: 18px; color: var(--ink); white-space: nowrap;
  }
  .swoosh { position: absolute; inset: 0; width: 100%; height: 100%; }
  .contacts {
    position: absolute; right: 24px; top: 182px;
    list-style: none; text-align: right; white-space: nowrap;
    color: var(--on-dark); font-size: 13px; line-height: 24px;
  }
  .contacts li { display: flex; justify-content: flex-end; align-items: center; gap: 10px; }
  .contacts svg { width: 14px; height: 14px; flex: none; }
</style>
</head>
<body>
<main class="sheet">

  <section class="card card-front" aria-label="Card front">
    <div class="photo" role="img" aria-label="Soft-focus photo of white hydrangea flower balls hanging from white wedding chairs along an aisle"></div>
    <div class="brand">
      <span class="brand-name">Fern Lattice</span>
      <span class="brand-tagline">Table and Chair Rentals</span>
    </div>
  </section>

  <section class="card card-back" aria-label="Card back">
    <div class="photo-faint" role="img" aria-label="Faded photo of wedding chairs with hanging flowers"></div>
    <svg class="swoosh" viewBox="0 0 540 300" aria-hidden="true">
      <path fill="var(--leaf-light)" d="M540 30 C470 34 440 70 400 100 C430 70 470 40 540 35 Z"/>
      <path fill="var(--leaf)" d="M540 38 C465 44 432 86 392 116 C343 153 302 165 252 190 C192 220 142 248 0 272 L0 280 C146 256 196 228 256 198 C306 173 347 161 396 124 C436 94 468 52 540 46 Z"/>
      <path fill="var(--earth)" d="M540 55 C470 60 440 100 400 130 C350 168 310 180 260 205 C200 235 150 262 0 287 L0 300 L540 300 Z"/>
    </svg>
    <span class="corner-name">Fern Lattice</span>
    <div class="brand">
      <span class="brand-name">Fern Lattice</span>
      <span class="brand-tagline">Table and Chair Rentals</span>
    </div>
    <ul class="contacts">
      <li>360-555-0182
        <svg viewBox="0 0 16 16" aria-hidden="true"><path fill="var(--on-dark)" d="M2 5c0-2 2-3 6-3s6 1 6 3v1h-3V5H5v1H2zM4 7h8l1 6H3z"/></svg>
      </li>
      <li>sales@fernlatticerentals.com
        <svg viewBox="0 0 16 16" aria-hidden="true"><rect x="1" y="3" width="14" height="10" fill="var(--on-dark)"/><path d="M1 3l7 6 7-6" fill="none" stroke="var(--earth)" stroke-width="1.2"/></svg>
      </li>
      <li>www.fernlatticerentals.com
        <svg viewBox="0 0 16 16" aria-hidden="true"><circle cx="8" cy="8" r="6.5" fill="none" stroke="var(--on-dark)" stroke-width="1.4"/><path d="M1.5 8h13M8 1.5c-3 3-3 10 0 13M8 1.5c3 3 3 10 0 13" fill="none" stroke="var(--on-dark)" stroke-width="1.1"/></svg>
      </li>
    </ul>
  </section>

</main>
</body>
</html>
```